Digital Recipe eBook Design

I need a recipe eBook designed for me. I have attached the recipes (see here https://pages.tarnovel.net/sheet/k/7Qp3XZ41TTb82Lr5mkdBvxhpJQ0NsoRPYcEAK63FXwtu/view?mode=public) and associated images in Google Drive (see images here https://store.plumvexa.com/store/bundles/83KTsQwund5Ho2Pcm6yvbrEXk0TZ?mode=public). I am open to any sort of ideas but want the recipe book to look highly professional and with a simple, yet sleek, design. I have included some examples of designs I like here: https://store.plumvexa.com/store/bundles/6R_Ty4GDqJpsm-NnbwuhLoEC0PZBk?mode=public

Target Market(s)

Women 20-35

Industry/Entity Type

Health And Wellness

Font styles to use
Sans Serif

Colors
e667a6
eea4c8
f9deeb

Requirements
Must have
• No typos
• Professional design
Should not have
• Overly decorative design - keep it simple and clean

```html
<!DOCTYPE html>
<html lang="en">
<head>
<meta charset="utf-8">
<title>The Bright Cycle Cookbook – Page Spread</title>
<link rel="stylesheet" href="https://fonts.googleapis.com/css2?family=Raleway:wght@300;400;600&family=Montserrat:wght@400;600;700&display=swap">
<style>
:root{
  --bg:#b3b3b3;
  --paper:#ffffff;
  --pink:#e667a6;
  --pink-mid:#eea4c8;
  --pink-soft:#f9deeb;
  --ink:#555555;
  --ink-soft:#888888;
}
*{margin:0;padding:0;box-sizing:border-box}
html,body{width:1200px;height:675px;overflow:hidden;background:var(--bg)}
body{position:relative;font-family:'Raleway',sans-serif;color:var(--ink)}
.page{position:absolute;width:208px;height:270px;background:var(--paper);overflow:hidden;box-shadow:0 1px 3px rgba(0,0,0,.18)}
.page::after{content:"";position:absolute;left:0;right:0;bottom:0;height:5px;background:var(--pink-mid)}
.page.full::after{display:none}
.photo{position:absolute}
.ph-green{background:linear-gradient(135deg,#3f6b2e,#c9c36a 55%,#e9e4d6)}
.ph-bowl{background:radial-gradient(circle at 45% 40%,#f1ede2 0 18%,#9dbb4a 35%,#e8b23d 55%,#cf5a2a 75%,#50622d)}
.ph-muffin{background:radial-gradient(circle at 30% 35%,#e8b866,#d86a3a 30%,#6b6660 60%,#3d3d3d)}
.ph-smoothie{background:linear-gradient(160deg,#dcdcdc,#a7775a 45%,#5b3a2a 70%,#cfc6bb)}
.ph-juice{background:linear-gradient(160deg,#e5e5e5,#9cbf3a 50%,#6f8f2a)}
.ph-cover{background:linear-gradient(135deg,#6f6f7a,#b49a78 25%,#5b4335 45%,#8fa3b8 60%,#a7b84a 75%,#d7cbb5)}
.band-top{position:absolute;left:0;right:0;top:0;height:5px;background:var(--pink-mid)}
.title-box{position:absolute;background:var(--pink-mid);color:#fff;font-weight:300;text-align:center;white-space:nowrap}
.h-ingr{position:absolute;color:var(--pink);font-weight:300;font-size:9px}
.h-how{position:absolute;color:var(--pink);font-weight:300;font-size:9px}
.list{position:absolute;font-size:4.3px;line-height:1.55;list-style:none;color:var(--ink)}
.list li::before{content:"• ";}
.steps{position:absolute;font-size:3.9px;line-height:1.6;color:var(--ink)}
.serves{position:absolute;font-size:3.8px;color:var(--pink)}
.overlay{position:absolute;background:rgba(238,164,200,.72);color:#fff;font-size:3.7px;line-height:1.65;text-align:justify;padding:5px 5px}
.note{position:absolute;font-size:3.7px;line-height:1.6;color:var(--pink)}

.cover-band{position:absolute;left:0;right:0;height:19px;background:var(--pink-mid);color:#fff;font-family:'Montserrat',sans-serif;font-size:6.6px;letter-spacing:1.3px;text-align:center;line-height:19px}
.cover-badge{position:absolute;left:56px;top:57px;width:96px;height:96px;border-radius:50%;background:var(--pink-mid);color:#fff;font-weight:300;font-size:13.5px;line-height:1.5;display:flex;align-items:center;justify-content:center;text-align:center}

.welcome-title{position:absolute;left:27px;top:46px;color:var(--pink);font-size:10px;font-weight:300}
.welcome-body{position:absolute;left:27px;top:82px;width:160px;font-size:3.5px;line-height:1.45;color:#444}
.welcome-body p{margin-bottom:3px}

.toc-tab{position:absolute;left:14px;top:38px;width:13px;height:192px;background:var(--pink-mid)}
.toc-tab span{position:absolute;left:50%;top:50%;transform:translate(-50%,-50%) rotate(-90deg);color:#fff;font-family:'Montserrat',sans-serif;font-weight:700;font-size:11px;letter-spacing:1.3px;white-space:nowrap}
.toc{position:absolute;left:54px;top:38px;width:130px}
.toc-dash{width:12px;height:3px;background:var(--pink-mid);margin-bottom:4px}
.toc h3{font-family:'Montserrat',sans-serif;font-size:4.2px;font-weight:600;letter-spacing:.4px;margin:4px 0 2px;color:#555}
.toc-row{display:flex;justify-content:space-between;font-size:3.6px;font-style:italic;line-height:1.8;color:#666}
.toc-row b{font-style:normal;font-weight:400}
</style>
</head>
<body>

<section class="page full cover" style="left:41px;top:61px">
  <div class="cover-band" style="top:0">Bloom Root Wellness</div>
  <div class="photo ph-cover" style="left:0;top:19px;width:208px;height:233px" role="img" aria-label="Grid of food photographs: desserts, seed crackers, bread, green juices, slices, salads and bliss balls"></div>
  <div class="cover-badge">The Bright<br>Cycle<br>Cookbook</div>
  <div class="cover-band" style="bottom:0">Lena Hartley</div>
</section>

<section class="page" style="left:268px;top:61px">
  <h1 class="welcome-title">Welcome</h1>
  <div class="welcome-body">
    <p><i>Food is foundational when it comes to hormone balance. What you eat directly contributes to how well your body creates new hormones, detoxifies used-up hormones and how regularly you ovulate.</i></p>
    <p>As you learn the importance of certain cycle-supporting foods in the Cycle Balance Academy modules, it can feel overwhelming if you haven't included these foods in your diet before.</p>
    <p>The aim of this cookbook is to take away the overwhelm and get you excited about the possibilities of eating these foods.</p>
    <p>I'm sharing with you simple and delicious ways to prepare these cycle-supporting ingredients, along with lots of tips and tricks to individualise each recipe.</p>
    <p>All of the recipes included in this cookbook are gluten free, dairy free and offer vegetarian alternatives. Once you are comfortable with these recipes, feel free to experiment with them by subbing in and out different ingredients such as the vegetables or proteins suggested. The sky is the limit!</p>
    <p><b>I would love to see what you create!</b> Tag me on Snapwall @bloomrootwellness or post in our Circlebook group when you make any of the recipes.</p>
    <p>Happy cooking!</p>
    <p>Lena.</p>
  </div>
</section>

<section class="page" style="left:500px;top:61px">
  <div class="band-top"></div>
  <div class="toc-tab"><span>TABLE OF CONTENTS</span></div>
  <div class="toc">
    <div class="toc-dash"></div>
    <h3>BREAKFAST</h3>
    <div class="toc-row">The Goddess Breakfast Bowl<b>5</b></div>
    <div class="toc-row">Meal-Prep Egg Muffins<b>7</b></div>
    <div class="toc-row">Chocolate Cauliflower Smoothie<b>9</b></div>
    <div class="toc-row">Green Detox Smoothie<b>11</b></div>
    <div class="toc-row">Buckwheat Porridge with Stewed Rhubarb<b>13</b></div>
    <h3>MAINS</h3>
    <div class="toc-row">Miso-Tahini Poke Bowl/Crispy<b>16</b></div>
    <div class="toc-row">Chickpea and Kale Salad<b>18</b></div>
    <div class="toc-row">The Simplest Gluten Free Buckwheat Bread<b>19</b></div>
    <div class="toc-row">Mexican Burrito Bowls<b>20</b></div>
    <div class="toc-row">One-Pan Salmon Pesto<b>21</b></div>
    <div class="toc-row">Antipasto Salad<b>22</b></div>
    <h3>SNACKS</h3>
    <div class="toc-row">Miso-Tahini Poke Bowl<b>23</b></div>
    <div class="toc-row">Crispy Chickpea and Kale Salad<b>24</b></div>
    <div class="toc-row">The Simplest Gluten Free Buckwheat Bread<b>26</b></div>
    <div class="toc-row">Mexican Burrito Bowls<b>27</b></div>
    <div class="toc-row">One-Pan Salmon Pesto<b>28</b></div>
    <div class="toc-row">Antipasto Salad<b>29</b></div>
    <h3>DRINKS</h3>
    <div class="toc-row">Descriptive Statistics<b>30</b></div>
    <div class="toc-row">Factor Analysis<b>31</b></div>
  </div>
</section>

<section class="page" style="left:728px;top:61px">
  <div class="photo ph-bowl" style="left:27px;top:61px;width:75px;height:66px" role="img" aria-label="Goddess breakfast bowl"></div>
  <div class="photo ph-smoothie" style="left:106px;top:61px;width:75px;height:66px" role="img" aria-label="Chocolate smoothie in a glass"></div>
  <div class="photo ph-muffin" style="left:27px;top:131px;width:75px;height:68px" role="img" aria-label="Egg muffins on a cooling rack"></div>
  <div class="photo ph-juice" style="left:106px;top:131px;width:75px;height:68px" role="img" aria-label="Green smoothies in jars"></div>
  <div class="title-box" style="left:54px;top:117px;width:100px;height:27px;font-size:19px;line-height:27px">Breakfast</div>
</section>

<section class="page" style="left:956px;top:61px">
  <div class="photo ph-green" style="left:0;top:0;width:208px;height:39px" role="img" aria-label="Close-up of greens, avocado and sweet potato"></div>
  <div class="title-box" style="left:43px;top:12px;width:120px;height:15px;font-size:8.5px;line-height:15px">Goddess Breakfast Bowl</div>
  <div class="photo ph-bowl" style="left:18px;top:61px;width:66px;height:53px" role="img" aria-label="Goddess breakfast bowl"></div>
  <div class="serves" style="left:18px;top:120px">Serves 1</div>
  <div class="h-ingr" style="left:113px;top:55px">Ingredients</div>
  <ul class="list" style="left:115px;top:71px;width:80px">
    <li>2 eggs (free range or organic where possible)</li>
    <li>¼ avocado</li>
    <li>½ small sweet potato, cubed (around ½ cup)</li>
    <li>2 florets of cauliflower</li>
    <li>Large handful of fresh greens (e.g. baby spinach)</li>
    <li>Drizzle of olive oil</li>
  </ul>
  <div class="h-how" style="left:18px;top:143px">How To:</div>
  <ol class="steps" style="left:18px;top:166px;width:172px;list-style-position:inside">
    <li>Boil a small saucepan of water and once boiling gently add the two eggs and set a timer for 6 minutes (for soft-boiled) or 10 minutes (for hard-boiled)</li>
    <li>Meanwhile, steam the sweet potato and cauliflower until just soft</li>
    <li>When the eggs are done, remove from the saucepan and place in an ice-cold bowl of water for 2-3 minutes (this makes the eggs easier to peel)</li>
    <li>Remove the eggs from the water and peel away their shells</li>
    <li>Assemble the bowl: place the greens at the bottom and top with eggs, sweet potato, cauliflower and avocado</li>
    <li>Garnish with salt and pepper and a drizzle of olive oil</li>
    <li>Enjoy!</li>
  </ol>
</section>

<section class="page full" style="left:41px;top:363px">
  <div class="photo ph-bowl" style="left:0;top:0;width:208px;height:270px" role="img" aria-label="Overhead photo of the goddess breakfast bowl with cauliflower, avocado, egg and sweet potato"></div>
  <div class="overlay" style="left:22px;top:176px;width:171px">
    This bowl is the ultimate balanced breakfast for your hormones that will keep you full all morning. Start your day by ticking all the hormone-balancing principals in one bowl!<br>
    • Healthy fats from avocado, egg yolks and olive oil<br>
    • Protein from eggs<br>
    • Complex carbohydrates from sweet potato<br>
    • Liver and cycle-supporting nutrients from cauliflower and greens<br><br>
    NOTE: This bowl can be prepared the night before for an easy grab-and-go breakfast
  </div>
</section>

<section class="page" style="left:268px;top:363px">
  <div class="photo ph-muffin" style="left:0;top:0;width:209px;height:39px" role="img" aria-label="Egg muffins on a rack"></div>
  <div class="title-box" style="left:43px;top:12px;width:108px;height:15px;font-size:8.5px;line-height:15px">Meal Prep Egg Muffins</div>
  <div class="photo ph-muffin" style="left:18px;top:50px;width:75px;height:54px" role="img" aria-label="Egg muffins on a cooling rack"></div>
  <div class="serves" style="left:18px;top:109px">Makes around 12 muffins</div>
  <div class="h-ingr" style="left:113px;top:45px">Ingredients</div>
  <ul class="list" style="left:115px;top:60px;width:80px">
    <li>1 cup chopped broccoli</li>
    <li>2 Tablespoons chopped onions</li>
    <li>1/4 cup chopped red capsicum</li>
    <li>8 eggs, whisked</li>
    <li>1/2 cup (120 ml) coconut milk</li>
    <li>Salt and pepper to taste</li>
  </ul>
  <div class="h-how" style="left:18px;top:126px">How To:</div>
  <ol class="steps" style="left:18px;top:144px;width:172px;list-style-position:inside">
    <li>Preheat oven to 180°C (350°F)</li>
    <li>Mix the vegetables, whisked eggs and coconut milk together in a large mixing bowl</li>
    <li>Pour batter into muffin cups (an average sized 12-capacity tray should fit the mixture)</li>
    <li>Bake for 25-30 minutes until the middle of the muffins are solid when touched</li>
    <li>Serve as is for an on-the-go breakfast or snack, or serve with a piece of toast and some avocado for a more filling breakfast</li>
  </ol>
  <div class="note" style="left:18px;top:209px;width:172px">
    Mix up the flavours<br><br>
    You can use any variety of chopped vegetables that you like. Get creative and add extra flavour with some of these additions: smoked salmon, crumbled goat's feta (if you tolerate dairy), fresh herbs e.g. basil or rosemary, dried herbs and spices e.g. paprika, roasted sweet potato, pumpkin or beetroot, pesto or other dips: add a teaspoon to each muffin tin after you pour in the mixture
  </div>
</section>

<section class="page full" style="left:499px;top:363px">
  <div class="photo ph-muffin" style="left:0;top:0;width:209px;height:270px" role="img" aria-label="Egg muffins cooling on a wire rack"></div>
  <div class="overlay" style="left:11px;top:205px;width:186px">
    These high protein muffins are a perfect Sunday meal prep recipe to set yourself up for a week of healthy breakfasts. Mix and match the filling ingredients with your favourite vegetables and proteins. Once cooked you can cool down and store portioned in the fridge for super simple on-the-go breakfasts or snacks throughout the day.
  </div>
</section>

<section class="page" style="left:729px;top:363px">
  <div class="photo ph-smoothie" style="left:0;top:0;width:209px;height:39px" role="img" aria-label="Cacao and smoothie close-up"></div>
  <div class="title-box" style="left:27px;top:12px;width:150px;height:15px;font-size:8.5px;line-height:15px;outline:1px solid var(--pink-mid);outline-offset:2px">Chocolate Cauliflower Smoothie</div>
  <div class="photo ph-smoothie" style="left:18px;top:70px;width:78px;height:64px" role="img" aria-label="Hand holding a chocolate smoothie"></div>
  <div class="serves" style="left:18px;top:142px">Serves 1</div>
  <div class="h-ingr" style="left:113px;top:42px">Ingredients</div>
  <ul class="list" style="left:115px;top:58px;width:80px">
    <li>¾ cup steamed cauliflower (cooled in the fridge) TIP: make a batch of cauliflower on the weekend for easy breakfasts</li>
    <li>1 banana, cut into chunks and frozen</li>
    <li>⅓ avocado</li>
    <li>½ cup coconut or almond milk</li>
    <li>2 Tbsp cacao powder</li>
    <li>1 scoop protein powder (I recommend vanilla or chocolate flavoured)</li>
  </ul>
  <div class="h-how" style="left:20px;top:183px">How To:</div>
  <ol class="steps" style="left:20px;top:200px;width:172px;list-style-position:inside">
    <li>Add all ingredients to a blender or food processor and blend until smooth. Enjoy straight away or store in the fridge for up to 1 day</li>
    <li>TIP: this recipe will make a thick smoothie that can be eaten with a spoon. For a thinner smoothie that can be drunk with a straw, increase the milk to around 1 cup</li>
  </ol>
</section>

<section class="page full" style="left:956px;top:363px">
  <div class="photo ph-smoothie" style="left:0;top:0;width:208px;height:270px" role="img" aria-label="Hand holding a glass of chocolate cauliflower smoothie"></div>
  <div class="overlay" style="left:12px;top:163px;width:184px">
    Don't be put off by the cauliflower! This rich chocolatey smoothie tastes like a decadent dessert, but secretly includes a liver-supporting dose of cauliflower that you truly cannot taste. The avocado in this smoothie makes it smooth and creamy plus supplies your body with healthy fats to create your hormones. Combining healthy fats from avocado, sweetness from bananas and protein powder to keep you full all morning, this smoothie meets all the hormone-balancing principals. Cauliflower is one of the best foods you can eat to support your liver's detoxification of excess hormones - helping you maintain balanced hormone levels.
  </div>
</section>

</body>
</html>
```